Road Construction Company needs business cards

We would like a new business card designed for our business.

We're a road construction company based in Qld, Australia.

Can the business card please have the following information on it.

Name: Warren Halbeck
Position: General Manager
Phone: 0472 915 348
Email: Warren.halbeck@tovrin.com.au
Address: 87 Marrow Ave, Pendlebay, QLD, 4023
Website: www.tovrin.com.au

Visually we'd like the card to be professional and simple.

Attached is our logo.

Our website is www.tovrin.com.au

Target Market(s)

Men aged 25-60

Contact Information for Business Card

As listed in project description

Font styles to use
Serif

Requirements
Must have
• Large logo on back of card

```html
<!DOCTYPE html>
<html lang="en">
<head>
<meta charset="utf-8">
<title>Tovrin Business Card</title>
<link href="https://fonts.googleapis.com/css2?family=Exo+2:wght@400;700;800&display=swap" rel="stylesheet">
<style>
  :root {
    --backdrop: #2b2b2b;
    --card-white: #ffffff;
    --navy: #0a4fa0;
    --sky: #33a6da;
    --ink: #1e1e1e;
    --back-dark: #0353a4;
    --back-light: #35a8da;
  }
  * { box-sizing: border-box; margin: 0; padding: 0; }
  html, body {
    width: 1093px; height: 1200px; overflow: hidden;
    background: var(--backdrop);
    font-family: "Exo 2", sans-serif;
  }
  .card {
    position: absolute;
    left: 258px;
    width: 578px;
    height: 357px;
    border-radius: 26px;
    overflow: hidden;
    box-shadow: 3px 4px 6px rgba(0,0,0,0.6);
  }
  .card-front { top: 226px; background: var(--card-white); }
  .card-back {
    top: 621px;
    background: linear-gradient(35deg, var(--back-dark) 0%, #1a7cc0 50%, var(--back-light) 100%);
  }
  .holder { position: absolute; left: 35px; top: 46px; }
  .holder-name {
    font-weight: 700; font-size: 21px; color: var(--navy);
    text-transform: uppercase; letter-spacing: -0.2px; line-height: 1;
  }
  .holder-role { font-size: 17px; color: var(--sky); line-height: 1.2; margin-top: 1px; }
  .brand-front {
    position: absolute; right: 32px; top: 30px;
    font-weight: 800; font-size: 46px; color: var(--navy);
    letter-spacing: 3px; line-height: 1;
  }
  .contact-list {
    position: absolute; left: 35px; top: 254px; list-style: none;
  }
  .contact-list li {
    display: flex; align-items: center; gap: 7px;
    font-size: 16px; color: var(--ink); height: 21px;
  }
  .contact-list svg { width: 16px; height: 16px; flex: none; }
  .contact-list .accent { color: var(--navy); }
  .address {
    position: absolute; right: 32px; top: 276px;
    text-align: right; font-size: 16px; color: var(--ink); line-height: 21px;
  }
  .base-band { position: absolute; left: 0; bottom: 0; width: 100%; height: 19px; }
  .brand-back {
    position: absolute; left: 0; right: 0; top: 145px;
    text-align: center; font-weight: 800; font-size: 62px;
    color: var(--card-white); letter-spacing: 5px; line-height: 1;
  }
</style>
</head>
<body>
  <section class="card card-front" aria-label="Business card front">
    <div class="holder">
      <p class="holder-name">Warren Halbeck</p>
      <p class="holder-role">General Manager</p>
    </div>
    <p class="brand-front">TOVRIN</p>
    <ul class="contact-list">
      <li>
        <svg viewBox="0 0 16 16" aria-hidden="true"><path fill="#0a4fa0" d="M3.2 1.5 5.6 4c.4.4.4 1 0 1.4l-1 1c.9 2 2.4 3.5 4.4 4.4l1-1c.4-.4 1-.4 1.4 0l2.5 2.4c.4.4.4 1 0 1.4l-1.2 1.2c-.7.7-1.8.9-2.7.5C6.3 14 2.1 9.8.7 6c-.4-.9-.2-2 .5-2.7Z"/><path fill="none" stroke="#0a4fa0" stroke-width="1.4" d="M9.5 1.5a5 5 0 0 1 5 5M9.3 4.3a2.4 2.4 0 0 1 2.4 2.4"/></svg>
        0472 915 348
      </li>
      <li>
        <svg viewBox="0 0 16 16" aria-hidden="true"><rect x="0.5" y="3" width="15" height="10" fill="#0a4fa0"/><path fill="none" stroke="#fff" stroke-width="1.2" d="M1 3.5l7 5.5 7-5.5M1 12.5l5-4.2M15 12.5l-5-4.2"/></svg>
        Warren.halbeck@tovrin.com.au
      </li>
      <li>
        <svg viewBox="0 0 16 16" aria-hidden="true"><g fill="none" stroke="#0a4fa0" stroke-width="1.3"><circle cx="8" cy="8" r="7"/><ellipse cx="8" cy="8" rx="3" ry="7"/><path d="M1 8h14M2 4.5h12M2 11.5h12"/></g></svg>
        <span>www.<span class="accent">tovrin</span>.com.au</span>
      </li>
    </ul>
    <p class="address">87 Marrow Ave<br>Pendlebay, QLD, 4023</p>
    <svg class="base-band" viewBox="0 0 578 19" preserveAspectRatio="none" aria-hidden="true">
      <polygon points="0,0 310,0 302,19 0,19" fill="var(--navy)"/>
      <polygon points="317,0 578,1 578,19 309,19" fill="var(--sky)"/>
    </svg>
  </section>

  <section class="card card-back" aria-label="Business card back">
    <p class="brand-back">TOVRIN</p>
  </section>
</body>
</html>
```